The 22 Rules and Traps of House Lending or the 22 things that will derail your transaction and how to prevent them.

I am looking to do a series of 4 to 5 e-books that should have a consistent format and theme

The first of these should be entitled, "The 22 Rules and Traps of House Lending" That is similar in style to the attached e-book.
The attached e-book is pretty much the style that I am looking for, The same format can be followed. I have attached a black and white head shot image for the head shot areas that appears on page two of the attached e-book. I have also attached my company logo.
Please feel free to use the same or similar colors in my logo for the lay-out of the e-book. However please do not feel limited to those colors. - Feel free to use your imagination.

The content can be found here.

http://www.fredtheloanfox.example/loan-advice.php

For the final “About” page of the e-book - Please entitle it… About Fred the Loan Fox.
The content for the last page can be found in the attached document - Owen Thistlewood bio2

The first page is where the creativity come in

Requirements
Must have
• Note that this project is for one e-book - However, once the designer and format is chosen the remainder of the projects will be launched

```html
<!DOCTYPE html>
<html lang="en">
<head>
<meta charset="utf-8">
<title>The 22 Rules and Traps of House Lending — Page 7</title>
<link href="https://fonts.googleapis.com/css2?family=Jost:wght@300;400;500;600;700;800&family=Cormorant+Garamond:wght@600;700&display=swap" rel="stylesheet">
<style>
  :root {
    --navy: #1f3977;
    --navy-dark: #14295e;
    --accent-red: #e5262a;
    --mid-blue: #4f6fb3;
    --body-text: #2d3a5c;
    --page: #ffffff;
  }
  * { margin: 0; padding: 0; box-sizing: border-box; }
  html, body { width: 900px; height: 1200px; overflow: hidden; background: var(--page); }
  .page {
    position: relative;
    width: 900px;
    height: 1200px;
    background: var(--page);
    font-family: "Jost", "Futura", sans-serif;
    color: var(--body-text);
  }
  .tip { position: absolute; left: 0; width: 900px; }
  .tip-number {
    position: absolute;
    left: 23px;
    top: 0;
    width: 48px;
    height: 48px;
    border-radius: 50%;
    background: var(--navy-dark);
    color: #fff;
    font-family: "Cormorant Garamond", Georgia, serif;
    font-weight: 700;
    font-size: 31px;
    line-height: 46px;
    text-align: center;
  }
  .tip-heading {
    margin-left: 64px;
    width: 780px;
    text-indent: 42px;
    font-family: "Jost", "Futura", sans-serif;
    font-weight: 400;
    font-size: 28.5px;
    line-height: 35px;
    color: var(--navy);
  }
  .tip-heading .dont { color: var(--accent-red); font-weight: 700; }
  .tip-heading .do { color: var(--mid-blue); font-weight: 700; }
  .tip-body {
    margin-left: 64px;
    width: 774px;
    font-weight: 300;
    font-size: 14.6px;
    line-height: 21.6px;
    color: var(--body-text);
    margin-top: 20px;
  }
  .tip-advice {
    margin-left: 64px;
    width: 770px;
    margin-top: 22px;
    font-weight: 700;
    font-size: 17px;
    line-height: 28.5px;
    color: var(--mid-blue);
  }
  .tip-13 { top: 60px; }
  .tip-14 { top: 437px; }
  .tip-15 { top: 702px; }

  .page-footer {
    position: absolute;
    left: 64px;
    right: 64px;
    top: 1094px;
    height: 40px;
    display: flex;
    align-items: center;
    color: var(--navy);
  }
  .brand {
    display: flex;
    align-items: center;
    gap: 7px;
    font-family: "Jost", sans-serif;
    font-weight: 600;
    font-size: 15px;
    color: var(--navy);
    letter-spacing: 0.2px;
  }
  .brand-mark { width: 10px; height: 10px; background: var(--navy); }
  .footer-divider { width: 2px; height: 34px; background: var(--navy); margin: 0 12px; }
  .footer-title, .footer-licence {
    font-family: "Cormorant Garamond", Georgia, serif;
    font-weight: 700;
    font-variant: small-caps;
    font-size: 17px;
    letter-spacing: 0.4px;
    color: var(--navy);
  }
  .footer-licence { margin-left: 46px; }
  .page-number {
    margin-left: auto;
    width: 24px;
    height: 28px;
    background: var(--navy-dark);
    color: #fff;
    font-family: "Jost", sans-serif;
    font-size: 15px;
    line-height: 28px;
    text-align: center;
  }
</style>
</head>
<body>
<main class="page">

  <section class="tip tip-13">
    <div class="tip-number">13</div>
    <h2 class="tip-heading"><span class="dont">Don’t</span> move large sums of money into different accounts or move money unnec-essarily.</h2>
    <p class="tip-body">When processing a loan, underwriters like to see clearly which accounts the funds for the down-payment and closing costs are coming from. If a borrower is in the habit of moving funds from one account to another, the accounting of the funds used to close the loan become more difficult to track and document. This leads to more underwriting time and more work on your part, as you may be asked to provide further explanation and documentation of your banking trans-actions in order to close the loan. While it is unlikely that your loan will be de-nied for this reason, it does slow down the underwriting process and leads to more time-consuming work for both the mortgage professional and the borrower.</p>
    <p class="tip-advice">When in doubt, simply avoid moving funds unnecessarily. If you absolutely need to move funds from one account to another, consult your mortgage profes-sional on how best to approach this problem so a documentation strategy can be devised before you move your funds.</p>
  </section>

  <section class="tip tip-14">
    <div class="tip-number">14</div>
    <h2 class="tip-heading"><span class="dont">Don’t</span> make any large or unusual deposits into any of your accounts during the underwriting process especially cash deposits.</h2>
    <p class="tip-body">As with moving funds into different accounts mentioned above, it is a general lending rule that all large deposits into your account must be “sourced” or docu-mented. This can slow down the underwriting process significantly and create more work for you and your mortgage professional. As mentioned above if you absolutely have to move funds or make large deposits please consult with your mortgage professional before doing so plan can be devised to help minimize the possible underwriting delays</p>
  </section>

  <section class="tip tip-15">
    <div class="tip-number">15</div>
    <h2 class="tip-heading"><span class="do">Do</span> thoroughly document any gifts.</h2>
    <p class="tip-body">On most transactions your are allowed to receive gift funds from family members for the purchase of a new home. However, those gift funds do need to be docu-mented throughly to avoid delays in underwriting. If you are planning to receive gift funds for the purchase of your house, please contact your mortgage profes-sional for advice, as it is much easier to properly document the movement of funds from the donor to the borrower before the funds have been transferred than to document the movement of the funds after the fact.</p>
  </section>

  <footer class="page-footer">
    <div class="brand"><span class="brand-mark"></span>Cedar Harbor Lending</div>
    <span class="footer-divider"></span>
    <span class="footer-title">The 22 Rules and Traps of House Lending</span>
    <span class="footer-licence">Licence MLO#40827</span>
    <span class="page-number">7</span>
  </footer>

</main>
</body>
</html>
```